www.marvenholt.com

Updating website so looks futristic but yet business like and easy to navigate, essentially a good landing page with a cool picture summing up what we do, and links to the following pages, all other pages on site to be updated, Exclusive Distributor of Brisk Forge Unique Fitness Equipment Products in UK & Ireland, www.crestvolley.co.uk Exclusive Partners & Distributors Of Crest Volley - Obstacle Races - Obstacle Hire - Obstacle Training - Adventure Events, www.goplumwick.co.uk Adventures That Inspire. We also Health Club / Facillity Consultancy

```html
<!DOCTYPE html>
<html lang="en">
<head>
<meta charset="utf-8">
<title>Marven Holt — Health, Wellness, Fitness</title>
<link href="https://fonts.googleapis.com/css2?family=Roboto+Condensed:wght@400;700&display=swap" rel="stylesheet">
<style>
  :root{
    --bg:#121212;
    --bg-glow:#1f1f1f;
    --text:#f2f2f2;
    --accent:#e8641e;
    --rule:#c9541a;
    --player-bar:#e02a1f;
  }
  *{box-sizing:border-box;margin:0;padding:0}
  html,body{width:960px;height:1200px;overflow:hidden}
  body{
    background:radial-gradient(ellipse at 70% 30%,var(--bg-glow),var(--bg) 60%),var(--bg);
    font-family:"Roboto Condensed",Arial Narrow,sans-serif;
    color:var(--text);
    position:relative;
  }
  .top-rule,.section-rule{
    position:absolute;left:160px;width:640px;height:2px;
    background:linear-gradient(90deg,transparent,var(--rule) 20%,var(--rule) 80%,transparent);
  }
  .top-rule{top:0}
  .section-title{
    position:absolute;font-weight:700;font-size:29px;letter-spacing:.3px;line-height:1;
  }
  .section-title::after{
    content:"";position:absolute;left:-3px;right:-14px;bottom:-10px;height:2px;background:var(--text);
  }
  .section-copy{
    position:absolute;width:372px;font-size:11.6px;line-height:16.4px;
  }
  .section-copy p+p{margin-top:16.4px}
  .brand{color:var(--accent)}
  .player{position:absolute;overflow:hidden;background:#0b0b0b}
  .player .frame{position:absolute;inset:0}
  .player-title{position:absolute;left:8px;top:7px;font-size:9px;color:#fff}
  .player-icons{position:absolute;right:8px;top:6px;display:flex;gap:8px}
  .controls{position:absolute;left:6px;right:6px;bottom:4px;height:16px;display:flex;align-items:center;gap:6px;font-size:6.5px;color:#fff}
  .controls .spacer{flex:1}
  .progress{position:absolute;left:6px;right:6px;bottom:21px;height:2px;background:rgba(255,255,255,.3)}
  .progress span{display:block;height:100%;background:var(--player-bar)}
  .more{position:absolute;left:8px;bottom:30px;font-size:5.5px;color:#fff}
  .play-btn{position:absolute;left:50%;top:50%;width:38px;height:26px;margin:-13px 0 0 -19px;border-radius:6px;background:rgba(20,20,20,.8)}
  .thumb{position:absolute}
</style>
</head>
<body>
  <div class="top-rule"></div>

  <!-- HEALTH -->
  <section class="health">
    <h2 class="section-title" style="left:60px;top:37px">HEALTH</h2>
    <div class="section-copy" style="left:54px;top:95px">
      <p><span class="brand">Marven Holt</span> long term success depends on the talents commitment and shared values of our people, Marven Holt is made of a unique hand picked team that will ensure the best possible service is delivered, as a company were passionate about delivering the best for our clients so we employ and partner with the best people who share that drive, passion and are led through the Marven Holt values in everything they do.</p>
      <p>Our philosophy is based on open genuine collaborations working with organisations, who like us have a can do attitude proactive approach and who want to win, with over 25 years experience in the Health, Wellness and Fitness Industry and many hundreds of happy clients we want to help build your business the right way!</p>
    </div>
    <div class="player" style="left:484px;top:93px;width:400px;height:193px">
      <div class="frame" role="img" aria-label="Video still of children sprinting at the start of an outdoor obstacle race" style="left:29px;right:29px;background:linear-gradient(160deg,#6f7f97 0%,#48505c 40%,#2a2622 75%,#1a1512 100%)"></div>
      <div class="player-title">Ridgeline Kids Race</div>
      <div class="player-icons">
        <svg width="9" height="9" viewBox="0 0 10 10"><circle cx="5" cy="5" r="4.5" fill="#fff"/><path d="M5 2.5V5l2 1" stroke="#222" fill="none"/></svg>
        <svg width="9" height="9" viewBox="0 0 10 10"><path d="M6 1l4 4-4 4V6.5C3 6.5 1.5 7.5 0 9.5 .5 6 2.5 4 6 3.5z" fill="#fff"/></svg>
        <svg width="9" height="9" viewBox="0 0 10 10"><circle cx="5" cy="5" r="4.5" fill="#fff"/><rect x="4.4" y="4" width="1.2" height="3.5" fill="#222"/><rect x="4.4" y="2.3" width="1.2" height="1.1" fill="#222"/></svg>
      </div>
      <div class="more">MORE VIDEOS</div>
      <div class="progress"><span style="width:17%"></span></div>
      <div class="controls">
        <svg width="7" height="7" viewBox="0 0 8 8"><path d="M1 0l7 4-7 4z" fill="#fff"/></svg>
        <svg width="8" height="7" viewBox="0 0 8 7"><path d="M0 2h2l2-2v7L2 5H0z" fill="#fff"/><path d="M5.5 1.5a3 3 0 010 4" stroke="#fff" fill="none"/></svg>
        <span>0:18 / 1:46</span><span class="spacer"></span>
        <span>CC</span><span>⚙</span><span>Clipstream</span>
        <svg width="7" height="7" viewBox="0 0 8 8"><path d="M0 3V0h3M5 0h3v3M8 5v3H5M3 8H0V5" stroke="#fff" fill="none"/></svg>
      </div>
    </div>
    <div class="thumb" role="img" aria-label="Photo of racers climbing a muddy slope" style="left:487px;top:318px;width:109px;height:73px;background:linear-gradient(150deg,#8a8a7c,#4c4a3f 60%,#3a2e2a)"></div>
    <div class="thumb" role="img" aria-label="Photo of a runner silhouetted at sunset on wet ground" style="left:607px;top:318px;width:107px;height:73px;background:linear-gradient(180deg,#3d3f45,#c9955a 45%,#6b5a4a 70%,#d8c7b0)"></div>
    <div class="thumb" role="img" aria-label="Photo of an obstacle course climbing frame under a blue sky" style="left:727px;top:318px;width:105px;height:73px;background:linear-gradient(180deg,#3c6fb8,#9fb9d8 45%,#4e6a3a 75%,#2f4526)"></div>
  </section>

  <div class="section-rule" style="top:453px"></div>

  <!-- WELLNESS -->
  <section class="wellness">
    <h2 class="section-title" style="left:51px;top:481px">WELLNESS</h2>
    <div class="section-copy" style="left:50px;top:533px">
      <p><span class="brand">Marven Holt</span> long term success depends on the talents commitment and shared values of our people, Marven Holt is made of a unique hand picked team that will ensure the best possible service is delivered, as a company were passionate about delivering the best for our clients so we employ and partner with the best people who share that drive, passion and are led through the Marven Holt values in everything they do.</p>
      <p>Our philosophy is based on open genuine collaborations working with organisations, who like us have a can do attitude proactive approach and who want to win, with over 25 years experience in the Health, Wellness and Fitness Industry and many hundreds of happy clients we want to help build your business the right way!</p>
    </div>
    <div class="player" style="left:490px;top:516px;width:384px;height:219px">
      <div class="frame" role="img" aria-label="Video still of a hand holding a small activity tracker in front of a red heart" style="background:radial-gradient(circle at 80% 20%,#d8333f 0 14%,transparent 15%),linear-gradient(135deg,#e4e4e4 0%,#9c9c9c 45%,#4a4a4a 100%)"></div>
      <div class="player-title" style="font-size:10px">Pulsewell Technology Programme</div>
      <div class="player-icons">
        <svg width="11" height="11" viewBox="0 0 10 10"><circle cx="5" cy="5" r="4.5" fill="#fff"/><path d="M5 2.5V5l2 1" stroke="#222" fill="none"/></svg>
        <svg width="11" height="11" viewBox="0 0 10 10"><path d="M6 1l4 4-4 4V6.5C3 6.5 1.5 7.5 0 9.5 .5 6 2.5 4 6 3.5z" fill="#fff"/></svg>
      </div>
      <div class="play-btn"><svg width="38" height="26" viewBox="0 0 38 26"><path d="M15 8l10 5-10 5z" fill="#fff"/></svg></div>
    </div>
    <div class="thumb" role="img" aria-label="Black and white photo of a city skyline" style="left:491px;top:748px;width:121px;height:97px;background:linear-gradient(180deg,#d9d9d9,#7a7a7a 50%,#2e2e2e)"></div>
    <div class="thumb" role="img" aria-label="Word cloud of values such as integrity, ethics and standards" style="left:622px;top:748px;width:120px;height:97px;background:linear-gradient(180deg,#f1ede6,#e3ddd2)"></div>
    <div class="thumb" role="img" aria-label="Photo of a business presenter in a meeting room" style="left:751px;top:748px;width:121px;height:97px;background:linear-gradient(135deg,#c7d6ea,#7e8fb0 50%,#3e4357)"></div>
  </section>

  <div class="section-rule" style="top:895px"></div>

  <!-- FITNESS -->
  <section class="fitness">
    <h2 class="section-title" style="left:53px;top:932px">FITNESS</h2>
    <div class="section-copy" style="left:52px;top:981px">
      <p><span class="brand">Marven Holt</span> long term success depends on the talents commitment and shared values of our people, Marven Holt is made of a unique hand picked team that will ensure the best possible service is delivered, as a company were passionate about delivering the best for our clients so we employ and partner with the best people who share that drive, passion and are led through the Marven Holt values in everything they do.</p>
      <p>Our philosophy is based on open genuine collaborations working with organisations, who like us have a can do attitude proactive approach and who want to win, with over 25 years experience in the Health, Wellness and Fitness Industry and many hundreds of happy clients we want to help build your business the right way!</p>
    </div>
    <div class="player" style="left:490px;top:969px;width:388px;height:217px">
      <div class="frame" role="img" aria-label="Video still of people training on incline fitness machines in a gym" style="left:32px;right:32px;background:linear-gradient(110deg,#3c9fc8 0%,#4d7f99 30%,#8d8c8a 55%,#e0e0de 80%,#6a6a6a 100%)"></div>
      <div class="player-title">Brisk Forge Elevate Circuit</div>
      <div class="player-icons">
        <svg width="10" height="10" viewBox="0 0 10 10"><circle cx="5" cy="5" r="4.5" fill="#fff"/><path d="M5 2.5V5l2 1" stroke="#222" fill="none"/></svg>
        <svg width="10" height="10" viewBox="0 0 10 10"><path d="M6 1l4 4-4 4V6.5C3 6.5 1.5 7.5 0 9.5 .5 6 2.5 4 6 3.5z" fill="#fff"/></svg>
      </div>
      <div style="position:absolute;left:2px;right:12px;top:135px;height:50px;background:rgba(30,30,30,.6)"></div>
      <div class="thumb" role="img" aria-label="Related video of treadmill training" style="left:12px;top:138px;width:70px;height:45px;background:linear-gradient(135deg,#7b8fa8,#3b3f4a)"></div>
      <div class="thumb" role="img" aria-label="Related video of a person exercising on a white background" style="left:84px;top:138px;width:70px;height:45px;background:linear-gradient(135deg,#fafafa,#cfd6da)"></div>
      <div class="thumb" role="img" aria-label="Related video of a gym class" style="left:156px;top:138px;width:70px;height:45px;background:linear-gradient(135deg,#8d7d6a,#3c352f)"></div>
      <div class="thumb" role="img" aria-label="Related video of outdoor training" style="left:228px;top:138px;width:70px;height:45px;background:linear-gradient(135deg,#6f8f4e,#3c4a30)"></div>
      <div class="thumb" role="img" aria-label="Related video of a studio set" style="left:300px;top:138px;width:62px;height:45px;background:linear-gradient(135deg,#2a6fb8,#141a2e)"></div>
      <div style="position:absolute;right:2px;top:136px;font-size:8px;color:#fff">×</div>
      <div class="progress"><span style="width:36%"></span></div>
      <div class="controls">
        <svg width="7" height="7" viewBox="0 0 8 8"><path d="M1 0l7 4-7 4z" fill="#fff"/></svg>
        <svg width="8" height="7" viewBox="0 0 8 7"><path d="M0 2h2l2-2v7L2 5H0z" fill="#fff"/><path d="M5.5 1.5a3 3 0 010 4" stroke="#fff" fill="none"/></svg>
        <span>0:21 / 1:13</span><span class="spacer"></span>
        <span>⚙</span><span>Clipstream</span>
        <svg width="7" height="7" viewBox="0 0 8 8"><path d="M0 3V0h3M5 0h3v3M8 5v3H5M3 8H0V5" stroke="#fff" fill="none"/></svg>
      </div>
    </div>
    <div class="thumb" role="img" aria-label="Photo of fitness equipment" style="left:494px;top:1196px;width:120px;height:10px;background:linear-gradient(90deg,#e6e6e6,#c8312a)"></div>
    <div class="thumb" role="img" aria-label="Photo of fitness equipment" style="left:628px;top:1196px;width:120px;height:10px;background:#ececec"></div>
    <div class="thumb" role="img" aria-label="Photo of fitness equipment" style="left:756px;top:1196px;width:120px;height:10px;background:linear-gradient(90deg,#f0f0f0,#8a8a8a)"></div>
  </section>
</body>
</html>
```